Automotive component supplier needs a business card design

We need a business card design for our company called Velran Global Components Ltd based in the UK. We are a supplier of interior and exterior components to premium car manufacturers such as Corvel Ashby, Hadley Fenn, Marquist and Tavarelli. We would like to see a modern business card design that uses the colour blue.

Target Market(s)

Premium automotive car manufacturers.

Industry/Entity Type

Automotive

Contact Information for Business Card

Company Name : Velran Global Components Limited
Address: 17 Marlow Yard, Upper Heath, Warwick, CV31 8QL, United Kingdom
Web Address : www.velrancomponents-example.co.uk

Font styles to use
Other font styles liked:
• Helvetica

Colors
3176b5
0255a3
85acd3
cfdeed
cee9f5
85cae6
34a6d7
0692cd
9bcb3c

Requirements
Must have
• Clear company logo and a mixture of blue colours.
Nice to have
• A high quality modern image.
Should not have
• Multiple colours.

```html
<!DOCTYPE html>
<html lang="en">
<head>
<meta charset="utf-8">
<title>Velran Global Components – Business Card</title>
<link rel="stylesheet" href="https://fonts.googleapis.com/css2?family=Arimo:wght@400;700&display=swap">
<style>
  :root {
    --backdrop: #dfe3e8;
    --card: #f4f6f9;
    --brand-blue: #0255a3;
    --band-light: #3176b5;
    --band-dark: #0255a3;
    --band-text: #cfdeed;
    --band-text-strong: #eef4fa;
    --accent-green: #9bcb3c;
  }
  * { box-sizing: border-box; margin: 0; padding: 0; }
  html, body {
    width: 1200px;
    height: 969px;
    overflow: hidden;
  }
  body {
    background: var(--backdrop);
    font-family: "Arimo", Helvetica, Arial, sans-serif;
    position: relative;
  }
  .business-card {
    position: absolute;
    left: 100px;
    top: 200px;
    width: 1000px;
    height: 569px;
    background: var(--card);
    box-shadow: 0 10px 30px rgba(20, 40, 70, 0.18);
    overflow: hidden;
  }
  .brand {
    position: absolute;
    left: 55px;
    top: 74px;
    color: var(--brand-blue);
    font-weight: 700;
    line-height: 1;
  }
  .brand-name {
    display: block;
    font-size: 84px;
    letter-spacing: 2px;
  }
  .brand-sub {
    display: block;
    font-size: 22px;
    letter-spacing: 1.5px;
    margin-top: 6px;
  }
  .contact-band {
    position: absolute;
    left: 0;
    top: 276px;
    width: 100%;
    height: 293px;
    background: linear-gradient(90deg, var(--band-light) 0%, var(--band-dark) 100%);
  }
  .accent-square {
    position: absolute;
    left: 950px;
    top: 276px;
    width: 46px;
    height: 34px;
    background: var(--accent-green);
    border-radius: 0 0 6px 6px;
  }
  .band-text {
    position: absolute;
    color: var(--band-text);
    font-size: 24px;
    line-height: 34px;
  }
  .address { left: 55px; top: 304px; }
  .company-contact { left: 55px; top: 442px; }
  .person { right: 52px; top: 340px; text-align: right; }
  .person-contact { right: 52px; top: 442px; text-align: right; }
  .label { font-weight: 700; }
  .person-name {
    font-size: 32px;
    font-weight: 700;
    color: var(--band-text-strong);
    letter-spacing: 0.5px;
    line-height: 38px;
  }
  .person-role { font-size: 24px; }
</style>
</head>
<body>
  <section class="business-card">
    <div class="brand">
      <span class="brand-name">VELRAN</span>
      <span class="brand-sub">GLOBAL COMPONENTS</span>
    </div>

    <div class="contact-band"></div>
    <div class="accent-square"></div>

    <address class="band-text address" style="font-style:normal">
      17 Marlow Yard, Upper Heath<br>
      Warwick, CV31 8QL<br>
      United Kingdom
    </address>

    <div class="band-text company-contact">
      <div><span class="label">Phone:</span> 689 512 7740</div>
      <div>www.velrancomponents-example.co.uk</div>
    </div>

    <div class="band-text person">
      <div class="person-name">DARREN HOLLOWAY</div>
      <div class="person-role">CEO/Founder</div>
    </div>

    <div class="band-text person-contact">
      <div><span class="label">Mobile:</span> 836 221 9057</div>
      <div>darren@velrancomponents-example.co.uk</div>
    </div>
  </section>
</body>
</html>
```